Brightmoor Lift Inc Website Deisgn

We are a new small elevator contracting company.
We would like a full website designed similar to
http://pellingtonlifts.com or https://www.northvalelifting.ca/
In addition to contents found on the above webpages.. we would like a section for project gallery etc.... have fun with it ... make it professional

Target Market(s)

Elevator Consultants - Property managers - Condo Boards - Commercial office buildings

Coding

Number of Pages Required

5+ page

Requirements
Must have
• Navigation Bar.. Be view able via mobile ..Should be pictures of Tall Office buildings in background.. Toronto city skyline etc....

Have Fun!

```html
<!DOCTYPE html>
<html lang="en">
<head>
<meta charset="utf-8">
<title>Brightmoor Lift Inc</title>
<link rel="stylesheet" href="https://fonts.googleapis.com/css2?family=Oswald:wght@400;500;600&family=Lato:wght@400;700&display=swap">
<style>
:root{
  --ink:#1f1f1f;
  --text:#4a4a4a;
  --muted:#7a7a7a;
  --accent:#f26b16;
  --light:#f1f1f1;
  --line:#8a8a8a;
  --dark:#151515;
  --darker:#0d0d0d;
  --white:#ffffff;
}
*{box-sizing:border-box;margin:0;padding:0}
html,body{width:1200px;height:4000px;overflow:hidden;background:var(--white)}
body{position:relative;font-family:'Lato',sans-serif;color:var(--text)}
.abs{position:absolute}

/* header */
.site-header{left:0;top:0;width:1200px;height:90px;background:var(--white)}
.brand{left:50px;top:24px;display:flex;align-items:center;gap:8px;white-space:nowrap}
.brand-dot{width:36px;height:36px;border:4px solid var(--ink);border-radius:50%;flex:none}
.brand-name{font-family:'Oswald',sans-serif;font-weight:600;font-size:22px;color:var(--ink);line-height:1;letter-spacing:.3px}
.nav{left:352px;top:34px;display:flex;gap:42px;font-family:'Oswald',sans-serif;font-size:16px;color:#555;white-space:nowrap}
.nav .active{color:var(--ink);border-bottom:2px solid var(--ink);padding-bottom:6px}
.nav-phone{left:993px;top:32px;display:flex;align-items:center;gap:8px;font-family:'Oswald',sans-serif;font-weight:500;font-size:18px;color:var(--ink);white-space:nowrap}

/* hero */
.hero{left:0;top:90px;width:1200px;height:618px;background:linear-gradient(180deg,#6d6d6d 0%,#9b9b9b 35%,#4d4d4d 70%,#2a2a2a 100%)}
.hero-kicker{left:0;width:1200px;top:262px;text-align:center;font-family:'Oswald',sans-serif;font-weight:500;font-size:66px;letter-spacing:8px;color:#cfcfcf}
.hero-title{left:0;width:1200px;top:330px;text-align:center;font-family:'Oswald',sans-serif;font-weight:400;font-size:96px;color:var(--white);letter-spacing:1px}
.hero-arrow{top:363px;width:52px;height:52px;border-radius:50%;background:#d9d9d9;display:flex;align-items:center;justify-content:center}

/* about */
.about-photo{left:160px;top:773px;width:352px;height:352px;border-radius:50%;background:radial-gradient(circle,#9a9a9a 0%,#4a4a4a 60%,#2b2b2b 100%)}
.about-title{left:562px;top:790px;font-family:'Oswald',sans-serif;font-weight:500;font-size:40px;color:var(--ink)}
.about-copy{left:563px;top:866px;width:540px;font-size:17.5px;line-height:25px;color:var(--text)}
.about-copy p+p{margin-top:28px}
.btn-outline{left:565px;top:1067px;width:155px;height:45px;border:2px solid var(--accent);color:var(--accent);font-family:'Oswald',sans-serif;font-size:16px;display:flex;align-items:center;justify-content:center}

/* services */
.services{left:0;top:1210px;width:1200px;height:638px;background:linear-gradient(180deg,#e6e6e6 0%,#cfcfcf 60%,#a9a9a9 100%)}
.section-title{left:0;width:1200px;text-align:center;font-family:'Oswald',sans-serif;font-weight:500;font-size:40px;color:#333}
.card{top:1352px;width:319px;height:401px;background:var(--white)}
.card-photo{height:205px}
.card h3{margin-top:24px;text-align:center;font-family:'Oswald',sans-serif;font-weight:400;font-size:21px;color:#333}
.card p{margin:12px auto 0;width:250px;text-align:center;font-size:12px;line-height:19px;color:#666}
.btn-dark{display:flex;margin:18px auto 0;width:144px;height:35px;background:var(--darker);color:var(--white);font-family:'Oswald',sans-serif;font-size:15px;align-items:center;justify-content:center}

/* gallery */
.tile{position:absolute}

/* faq */
.faq{left:0;top:2508px;width:1200px;height:575px;background:var(--light)}
.faq-item{left:180px;width:824px;border:2px solid var(--line);background:var(--light)}
.faq-q{position:absolute;left:28px;top:15px;font-size:17.5px;color:#333}
.faq-q.link{color:#1c3a6b;font-size:16px}
.faq-sign{position:absolute;right:22px;top:10px;font-family:'Lato',sans-serif;font-weight:700;font-size:24px;color:#222}
.faq-a{position:absolute;left:28px;top:50px;width:720px;font-size:14px;line-height:18px;color:#555}

/* booking */
.booking{left:0;top:3083px;width:1200px;height:495px;background:linear-gradient(180deg,#f4f4f4 0%,#bcbcbc 40%,#5c5c5c 100%)}
.booking-box{left:347px;top:3197px;width:504px;height:278px;background:rgba(30,30,30,.88);text-align:center;color:var(--white)}
.booking-box h2{margin-top:38px;font-family:'Oswald',sans-serif;font-weight:400;font-size:37px}
.booking-box p{margin:10px auto 0;width:420px;font-size:15px;line-height:19px;color:#ddd}
.btn-fill{display:flex;margin:16px auto 0;width:174px;height:40px;background:var(--accent);color:var(--white);font-family:'Oswald',sans-serif;font-size:19px;align-items:center;justify-content:center}
.booking-call{margin-top:20px;font-size:17px}

/* footer */
.footer{left:0;top:3578px;width:1200px;height:347px;background:var(--dark);color:var(--white)}
.footer-brand{left:108px;top:3680px;display:flex;align-items:center;gap:8px;white-space:nowrap}
.footer-brand .brand-dot{border-color:var(--white);width:40px;height:40px}
.footer-brand .brand-name{color:var(--white);font-size:24px}
.footer-about{left:113px;top:3750px;width:260px;font-size:13px;line-height:19px;color:#ccc}
.footer-head{font-family:'Oswald',sans-serif;font-weight:500;font-size:21px;color:var(--white)}
.footer-list{list-style:none;font-size:13px;color:#ddd}
.contact-list li{display:flex;align-items:center;gap:12px;height:34px;white-space:nowrap}
.company-list li{height:27px}
.subscribe{left:885px;top:3713px;width:222px;height:37px;background:#2a2a2a;display:flex}
.subscribe span{flex:1;padding:12px 14px;font-size:11px;color:#ccc}
.subscribe b{width:30px;background:var(--accent);display:flex;align-items:center;justify-content:center}
.social{left:887px;top:3775px;display:flex;gap:33px}
.social i{width:22px;height:22px;border-radius:50%;background:#dcdcdc;display:block}
.bottom-bar{left:0;top:3925px;width:1200px;height:75px;background:#1c1c1c;text-align:center;padding-top:27px;font-size:13px;color:#aaa}
</style>
</head>
<body>

<header class="site-header abs">
  <div class="brand abs"><span class="brand-dot"></span><span class="brand-name">BRIGHTMOOR LIFT INC</span></div>
  <nav class="nav abs">
    <span class="active">HOME</span><span>ABOUT US</span><span>OUR SERVICES</span><span>FREE QUOTE</span><span>GALLERY</span><span>CONTACT</span>
  </nav>
  <div class="nav-phone abs">
    <svg width="18" height="18" viewBox="0 0 24 24"><path fill="#f26b16" d="M6.6 10.8a15 15 0 0 0 6.6 6.6l2.2-2.2c.3-.3.7-.4 1-.2 1.1.4 2.3.6 3.6.6.6 0 1 .4 1 1V20c0 .6-.4 1-1 1A17 17 0 0 1 3 4c0-.6.4-1 1-1h3.5c.6 0 1 .4 1 1 0 1.3.2 2.5.6 3.6.1.3 0 .7-.2 1z"/></svg>
    (555) 014 2280
  </div>
</header>

<section class="hero abs" role="img" aria-label="Black and white photo of a downtown city skyline with a tall tower over the waterfront"></section>
<div class="hero-kicker abs">WELCOME TO</div>
<div class="hero-title abs">BRIGHTMOOR LIFT</div>
<div class="hero-arrow abs" style="left:35px"><svg width="18" height="18" viewBox="0 0 24 24"><path d="M15 4 7 12l8 8" stroke="#222" stroke-width="3" fill="none"/></svg></div>
<div class="hero-arrow abs" style="left:1122px"><svg width="18" height="18" viewBox="0 0 24 24"><path d="m9 4 8 8-8 8" stroke="#222" stroke-width="3" fill="none"/></svg></div>

<div class="about-photo abs" role="img" aria-label="Circular black and white photo of an elevator shaft interior"></div>
<h2 class="about-title abs">BRIGHTMOOR LIFT</h2>
<div class="about-copy abs">
  <p>Pellentesque faucibus Ut accumsan ultricies elit Maecenas at justo id velit placerat molestie Donec dictum lectus non odio Cras a ante vitae enim iaculis aliquam</p>
  <p>Mauris nunc quam venenatis nec euismod sit amet egestas placerat est Pellentesque habitant morbi tristique senectus et netus et malesuada fames ac turpis egestas Cras id elit</p>
</div>
<a class="btn-outline abs">LEARN MORE</a>

<section class="services abs" role="img" aria-label="Faded grey photo of city towers behind the services section"></section>
<h2 class="section-title abs" style="top:1264px">OUR SERVICES</h2>
<article class="card abs" style="left:98px">
  <div class="card-photo" role="img" aria-label="Photo of an elevator car viewed inside its shaft" style="background:linear-gradient(160deg,#5a4a3a,#2a2320 60%,#8a7a68)"></div>
  <h3>SERVICE &amp; REPAIR</h3>
  <p>consectetuer augue nisi quis lacus Ut ac mi quis lacus mollis aliquam Curabitur iaculis tempus eros Curabitur</p>
  <a class="btn-dark">LEARN MORE</a>
</article>
<article class="card abs" style="left:438px">
  <div class="card-photo" role="img" aria-label="Photo looking up at glass office towers against a blue sky" style="background:linear-gradient(160deg,#3f8fd6,#1d4f9a 55%,#9cc8ef)"></div>
  <h3>MODERNIZATION</h3>
  <p>consectetuer augue nisi quis lacus Ut ac mi quis lacus mollis aliquam Curabitur iaculis tempus eros Curabitur</p>
  <a class="btn-dark">LEARN MORE</a>
</article>
<article class="card abs" style="left:781px">
  <div class="card-photo" role="img" aria-label="Photo of a technician working in an elevator shaft" style="background:linear-gradient(160deg,#9a9a9a,#5e5e5e 60%,#b5b5b5)"></div>
  <h3>OTHER SERVICES</h3>
  <p>consectetuer augue nisi quis lacus Ut ac mi quis lacus mollis aliquam Curabitur iaculis tempus eros Curabitur</p>
  <a class="btn-dark">LEARN MORE</a>
</article>

<h2 class="section-title abs" style="top:1892px">OUR GALLERY</h2>
<div class="tile" style="left:113px;top:1977px;width:240px;height:223px;background:linear-gradient(160deg,#5f9fe0,#2a5fa8 60%,#bcd6ee)" role="img" aria-label="Photo of a glass office tower"></div>
<div class="tile" style="left:113px;top:2203px;width:240px;height:222px;background:linear-gradient(160deg,#8ab8e8,#1f4f96 55%,#0f2e60)" role="img" aria-label="Photo of twin glass towers"></div>
<div class="tile" style="left:355px;top:1977px;width:239px;height:448px;background:linear-gradient(170deg,#2a66b8,#123b7e 55%,#7fa9dc)" role="img" aria-label="Photo of a tall blue skyscraper"></div>
<div class="tile" style="left:597px;top:1977px;width:481px;height:223px;background:linear-gradient(150deg,#1b4a7a,#5c8fbf 50%,#123457)" role="img" aria-label="Photo looking up between glass skyscrapers"></div>
<div class="tile" style="left:597px;top:2203px;width:239px;height:222px;background:linear-gradient(160deg,#3d7ac0,#1c4f88 60%,#4aa0a0)" role="img" aria-label="Photo of angled glass buildings"></div>
<div class="tile" style="left:838px;top:2203px;width:240px;height:222px;background:linear-gradient(160deg,#2b2b2b,#6a6a6a 55%,#1a1a1a)" role="img" aria-label="Dark photo of office towers"></div>

<section class="faq abs"></section>
<h2 class="section-title abs" style="top:2552px">FAQ</h2>
<div class="faq-item abs" style="top:2633px;height:56px"><span class="faq-q">Nunc tempus felis vitae urna Vivamus porttitor ?</span><span class="faq-sign">+</span></div>
<div class="faq-item abs" style="top:2698px;height:56px"><span class="faq-q">Phasellus pellentesque aliquam enim Proin dui lectus cursus?</span><span class="faq-sign">+</span></div>
<div class="faq-item abs" style="top:2763px;height:108px"><span class="faq-q">Morbi eget arcu Morbi porta libero ?</span><span class="faq-sign">&minus;</span><span class="faq-a">Pellentesque faucibus Ut accumsan ultricies elit Maecenas at justo id velit placerat molestie Donec dictum lectus non odio Cras a ante vitae enim iaculis aliquam Mauris nunc quam venenatis nec</span></div>
<div class="faq-item abs" style="top:2878px;height:56px"><span class="faq-q link">Fusce tellus Sed metus augue convallis et vehicula?</span><span class="faq-sign">+</span></div>
<div class="faq-item abs" style="top:2940px;height:56px"><span class="faq-q link">Nunc tempus felis vitae urna Vivamus porttitor neque ?</span><span class="faq-sign">+</span></div>

<section class="booking abs" role="img" aria-label="Black and white aerial photo of downtown towers and highways"></section>
<div class="booking-box abs">
  <h2>BOOK APPOINTMENT</h2>
  <p>Augiat in pede Fusce tellus Sed metus augue convallis et vehicula ut pulvinar eu ante Integer orci</p>
  <a class="btn-fill">BOOK NOW</a>
  <div class="booking-call">or Call Us (555) 019 4471</div>
</div>

<footer class="footer abs"></footer>
<div class="footer-brand abs"><span class="brand-dot"></span><span class="brand-name">BRIGHTMOOR LIFT INC</span></div>
<p class="footer-about abs">Augiat in pede Fusce tellus Sed metus augue convallis et vehicula ut pulvinar eu ante Integer orci tellus tristiqu</p>
<div class="abs" style="left:440px;top:3667px">
  <h4 class="footer-head">CONTACT</h4>
  <ul class="footer-list contact-list" style="margin-top:14px">
    <li><svg width="16" height="16" viewBox="0 0 24 24"><path fill="#fff" d="M6.6 10.8a15 15 0 0 0 6.6 6.6l2.2-2.2c.3-.3.7-.4 1-.2 1.1.4 2.3.6 3.6.6.6 0 1 .4 1 1V20c0 .6-.4 1-1 1A17 17 0 0 1 3 4c0-.6.4-1 1-1h3.5c.6 0 1 .4 1 1 0 1.3.2 2.5.6 3.6.1.3 0 .7-.2 1z"/></svg>Phone (555) 014 2280</li>
    <li><svg width="16" height="18" viewBox="0 0 16 22"><rect x="2" y="1" width="12" height="20" rx="2" fill="none" stroke="#fff" stroke-width="2"/><circle cx="8" cy="17" r="1.3" fill="#fff"/></svg>Cell (555) 016 3390</li>
    <li><svg width="18" height="14" viewBox="0 0 18 14"><rect width="18" height="14" fill="#fff"/><path d="M0 0l9 7 9-7" stroke="#151515" stroke-width="1.6" fill="none"/></svg>hello@brightmoorlift.example</li>
  </ul>
</div>
<div class="abs" style="left:731px;top:3667px">
  <h4 class="footer-head">COMPANY</h4>
  <ul class="footer-list company-list" style="margin-top:12px">
    <li>About</li><li>Services</li><li>Blogs</li><li>Gallery</li><li>Contact Us</li>
  </ul>
</div>
<h4 class="footer-head abs" style="left:884px;top:3667px">SUBSCRIBE</h4>
<div class="subscribe abs"><span>Email address</span><b><svg width="14" height="14" viewBox="0 0 24 24"><path fill="#fff" d="M22 2 2 11l9 2 2 9z"/></svg></b></div>
<div class="social abs"><i></i><i></i><i></i><i></i></div>
<div class="bottom-bar abs">&copy; 2020 Company Name | All Rights Reserved</div>

</body>
</html>
```